Spring Detox sale graphics for social media

You MUST read the Brief in the WORD document and follow the instructions there. I want to create 10 social media graphics (new Instagram size 4:5 (1080 x 1350 pixels) focusing on our Mother’s Day Spring Detox Sale graphics, using any of the pics attached. Use the attached pics, NO RANDOM STOCK PHOTOGRAPHY. For the color scheme of the graphics, they should all be complementary to the product colors or feel like Spring time.

Target Market(s)

primarily women

Requirements
Must have
• the photos and text attached

```html
<!DOCTYPE html>
<html lang="en">
<head>
<meta charset="utf-8">
<title>Mother's Day Spring Detox Sale</title>
<link rel="stylesheet" href="https://fonts.googleapis.com/css2?family=Montserrat:wght@500&display=swap">
<style>
  :root {
    --plum: #7a3a69;
    --berry: #a5456f;
    --rose: #cf5379;
    --blush: #ec6086;
    --glow: rgba(255, 235, 242, 0.55);
    --white: #ffffff;
  }
  html, body {
    margin: 0;
    padding: 0;
    width: 960px;
    height: 1200px;
    overflow: hidden;
  }
  .sale-post {
    position: relative;
    width: 960px;
    height: 1200px;
    overflow: hidden;
    background:
      radial-gradient(ellipse 300px 260px at 90px 40px, var(--glow), transparent 70%),
      radial-gradient(ellipse 300px 260px at 880px 40px, var(--glow), transparent 70%),
      radial-gradient(ellipse 340px 300px at 40px 1180px, var(--glow), transparent 70%),
      radial-gradient(ellipse 340px 300px at 920px 1180px, var(--glow), transparent 70%),
      linear-gradient(180deg, var(--plum) 0%, var(--berry) 40%, var(--rose) 70%, var(--blush) 100%);
  }
  .sale-post__frame {
    position: absolute;
    left: 28px;
    top: 35px;
    width: 898px;
    height: 1123px;
    border: 3px solid var(--white);
  }
  .sale-post__headline {
    position: absolute;
    left: 0;
    right: 0;
    top: 293px;
    margin: 0;
    text-align: center;
    color: var(--white);
    font-family: "Montserrat", sans-serif;
    font-weight: 500;
    font-size: 89px;
    line-height: 119.5px;
    text-transform: uppercase;
    letter-spacing: 0;
  }
</style>
</head>
<body>
  <main class="sale-post">
    <div class="sale-post__frame"></div>
    <h1 class="sale-post__headline">25% Off<br>Mother’s Day<br>Sale: Detox This<br>Spring. Shine<br>This Summer</h1>
  </main>
</body>
</html>
```